Modern card design needed for building development company

We are looking for a sharp modern new look for our business cards.
We are a New Zealand based company called TKR Ventures NZ LTD that specialises in subdividing large sections, housing and commercial buildings.
We have attached a photo of the current logo and would like to see it improved somehow as it looks a bit dated.
We are open to any colours.

Target Market(s)

Investors, Property buyers

Industry/Entity Type

Investment

Contact Information for Business Card

TKR VENTURES NZ LTD
www.tkrventuresnz.co.nz

Damon Whitcombe
Phone +64 21 938 104
Email dpwhitcombe@korumail.co.nz

Font styles to use
Serif
Sans Serif

Colors
0792cd
33a6d7
85cae6
6b449b
886aae
f04a50
ec1f27
f37122
f68d4d

Requirements
Must have
• Please try and make the logo more modern or if you have a similar one we would like to see it.

```html
<!DOCTYPE html>
<html lang="en">
<head>
<meta charset="utf-8">
<title>TKR Ventures NZ LTD – Business Card</title>
<link href="https://fonts.googleapis.com/css2?family=Cinzel:wght@500&family=Work+Sans:wght@400;500;600&display=swap" rel="stylesheet">
<style>
  :root {
    --brand-red: #9a1a2a;
    --card-white: #ffffff;
    --stage: #2b2b2d;
    --ink-light: #ffffff;
  }
  * { box-sizing: border-box; margin: 0; padding: 0; }
  html, body {
    width: 1200px; height: 900px; overflow: hidden;
    background: var(--stage);
    font-family: "Work Sans", Arial, sans-serif;
  }
  .canvas { position: relative; width: 1200px; height: 900px; }

  .card {
    position: absolute;
    width: 660px; height: 377px;
    border-radius: 22px;
    overflow: hidden;
    box-shadow: 0 14px 30px rgba(0,0,0,.45);
  }
  .card--front { left: 330px; top: 48px; background: var(--brand-red); }
  .card--back  { left: 210px; top: 470px; background: var(--brand-red); }

  /* wordmark */
  .wordmark {
    font-family: "Cinzel", Georgia, serif;
    font-weight: 500;
    letter-spacing: 2px;
    display: flex; align-items: center; gap: 12px;
    white-space: nowrap;
  }
  .wordmark__square { width: 14px; height: 14px; }
  .card--front .wordmark {
    position: absolute; left: 50%; top: 50%;
    transform: translate(-50%, -50%);
    color: var(--ink-light); font-size: 30px;
  }
  .card--front .wordmark__square { background: var(--ink-light); }

  /* back */
  .back__top {
    position: absolute; left: 0; top: 0; width: 100%; height: 165px;
    background: var(--card-white);
  }
  .back__pointer {
    position: absolute; left: 62px; top: 164px;
    width: 0; height: 0;
    border-left: 11px solid transparent;
    border-right: 11px solid transparent;
    border-top: 14px solid var(--card-white);
  }
  .card--back .wordmark {
    position: absolute; right: 34px; top: 112px;
    color: var(--brand-red); font-size: 22px;
  }
  .card--back .wordmark__square { background: var(--brand-red); width: 11px; height: 11px; }

  .holder-name {
    position: absolute; left: 56px; top: 200px;
    color: var(--ink-light);
    font-size: 30px; font-weight: 600; letter-spacing: .3px;
  }
  .contact-list {
    position: absolute; left: 56px; top: 262px;
    list-style: none; color: var(--ink-light); font-size: 19px; line-height: 30px;
  }
  .contact-list li { display: flex; align-items: center; gap: 12px; }
  .contact-list svg { width: 14px; height: 14px; flex: none; }

  .company-block {
    position: absolute; right: 40px; bottom: 36px;
    text-align: right; color: var(--ink-light);
    font-size: 18px; line-height: 26px; letter-spacing: .6px;
  }
</style>
</head>
<body>
<main class="canvas">

  <section class="card card--front" aria-label="Card front">
    <div class="wordmark"><span class="wordmark__square"></span>TKR VENTURES NZ LTD</div>
  </section>

  <section class="card card--back" aria-label="Card back">
    <div class="back__top"></div>
    <div class="back__pointer"></div>
    <div class="wordmark"><span class="wordmark__square"></span>TKR VENTURES NZ LTD</div>

    <h1 class="holder-name">DAMON WHITCOMBE</h1>

    <ul class="contact-list">
      <li>
        <svg viewBox="0 0 24 24" aria-hidden="true"><path fill="#fff" d="M6.6 10.8a15 15 0 0 0 6.6 6.6l2.2-2.2a1 1 0 0 1 1-.25 11.4 11.4 0 0 0 3.6.57 1 1 0 0 1 1 1V20a1 1 0 0 1-1 1A17 17 0 0 1 3 4a1 1 0 0 1 1-1h3.5a1 1 0 0 1 1 1c0 1.25.2 2.45.57 3.57a1 1 0 0 1-.25 1z"/></svg>
        +64 21 938 104
      </li>
      <li>
        <svg viewBox="0 0 24 24" aria-hidden="true"><rect x="2.5" y="5" width="19" height="14" rx="1.5" fill="none" stroke="#fff" stroke-width="2"/><path d="M3 6l9 7 9-7" fill="none" stroke="#fff" stroke-width="2"/></svg>
        dpwhitcombe@korumail.co.nz
      </li>
    </ul>

    <div class="company-block">
      <p>TKR VENTURES NZ LTD</p>
      <p>www.tkrventuresnz.co.nz.com</p>
    </div>
  </section>

</main>
</body>
</html>
```